Stylish business cards for KV7

To create an appealing and professional business card design for a WOMEN Owned Construction Supply Company.
2 sided card. Incorporate brand elements, curvy, colorful, sleek and bright. No solid white background. attached samples of styles added shapes/ribbons. Want something with that WOW that looks awesome, factor. It is a new logo, so feel free to mess with logo colors in the blue and teal factors that can look good with both dark and light background. If you want to try a watermark with just the KV7, without the "Supply" that might look cool to.

Industry/Entity Type

Women owned construction supply company

Contact Information for Business Card

Name, Title, and phone number and email, web page. maybe spot for qr code.

Font styles to use
Sans Serif

Requirements
Nice to have
• would love to see colors, maybe stylish ribbon dividers or some sort of 2 or 3 tone color card that compliments logo.
Should not have
• Please do not have all white background. Do not include Home/reale state/ or building images.

```html
<!DOCTYPE html>
<html lang="en">
<head>
<meta charset="utf-8">
<title>KV7 Supply business cards</title>
<link rel="stylesheet" href="https://fonts.googleapis.com/css2?family=Montserrat:wght@400;500;700&display=swap">
<style>
  :root {
    --stage: #1c1c1e;
    --card-light: #f3f3f3;
    --navy: #1b3656;
    --navy-deep: #17304e;
    --teal: #2396b8;
    --ink: #3a3f45;
    --watermark-light: rgba(190, 198, 205, 0.45);
    --watermark-dark: rgba(255, 255, 255, 0.07);
    --white: #ffffff;
  }
  * { margin: 0; padding: 0; box-sizing: border-box; }
  html, body {
    width: 1200px; height: 1059px; overflow: hidden;
    background: var(--stage);
    font-family: "Montserrat", sans-serif;
  }
  .card {
    position: absolute;
    left: 255px;
    width: 690px;
    height: 392px;
    border-radius: 18px;
    overflow: hidden;
  }
  .card--front { top: 89px; background: var(--card-light); }
  .card--back { top: 547px; background: var(--navy); }

  .brand-name {
    position: absolute;
    font-weight: 700;
    white-space: nowrap;
    line-height: 1;
  }
  .card--front .brand-name {
    left: 38px; top: 70px;
    font-size: 40px;
    color: var(--navy);
  }
  .watermark {
    position: absolute;
    font-weight: 700;
    line-height: 1;
    white-space: nowrap;
    pointer-events: none;
  }
  .card--front .watermark {
    left: 340px; top: 150px;
    font-size: 190px;
    color: var(--watermark-light);
  }
  .card--back .watermark {
    left: -10px; top: 150px;
    font-size: 210px;
    color: var(--watermark-dark);
  }
  .accent-bar {
    position: absolute;
    left: 0; top: 184px;
    width: 18px; height: 34px;
    background: var(--teal);
  }
  .person-name {
    position: absolute;
    left: 38px; top: 188px;
    font-size: 21px; font-weight: 700;
    color: var(--navy);
    letter-spacing: 0.2px;
  }
  .person-title {
    position: absolute;
    left: 38px; top: 214px;
    font-size: 14px;
    color: var(--ink);
  }
  .address {
    position: absolute;
    left: 38px; top: 238px;
    font-size: 14.5px; line-height: 20px;
    color: var(--ink);
  }
  .contact-list {
    position: absolute;
    left: 38px; top: 290px;
    list-style: none;
    font-size: 14.5px;
    color: var(--ink);
  }
  .contact-list li {
    display: flex; align-items: center;
    height: 25px;
  }
  .contact-list svg { width: 13px; height: 13px; margin-right: 6px; flex: none; }

  .card--back .brand-name {
    left: 50%; top: 50%;
    transform: translate(-50%, -50%);
    font-size: 64px;
    color: var(--white);
  }
</style>
</head>
<body>
  <section class="card card--front" aria-label="Business card front">
    <div class="watermark" aria-hidden="true">KV7</div>
    <div class="brand-name">KV7 Supply</div>
    <div class="accent-bar"></div>
    <h1 class="person-name">DARLENE VOSS</h1>
    <p class="person-title">CEO/Founder</p>
    <p class="address">P.O Box 3170 Harbour Road<br>Westfield AB 40218</p>
    <ul class="contact-list">
      <li>
        <svg viewBox="0 0 16 16" aria-hidden="true"><path fill="#2396b8" d="M3.5 1l2.5 3-1.5 1.6c.9 2 2.4 3.5 4.4 4.4L10.5 8.5l3 2.5-1.2 2.6C7 13.5 2.5 9 2.4 3.7z"/></svg>
        555.018.2247
      </li>
      <li>
        <svg viewBox="0 0 16 16" aria-hidden="true"><rect x="1" y="3" width="14" height="10" fill="#2396b8"/><path d="M1 3l7 6 7-6" fill="none" stroke="#f3f3f3" stroke-width="1.3"/></svg>
        info@kv7supply.com.au
      </li>
      <li>
        <svg viewBox="0 0 16 16" aria-hidden="true"><g fill="none" stroke="#2396b8" stroke-width="1.3"><circle cx="8" cy="8" r="6.5"/><ellipse cx="8" cy="8" rx="3" ry="6.5"/><path d="M1.5 8h13M2.5 5h11M2.5 11h11"/></g></svg>
        www.kv7supply.com.au
      </li>
    </ul>
  </section>

  <section class="card card--back" aria-label="Business card back">
    <div class="watermark" aria-hidden="true">KV7</div>
    <div class="brand-name">KV7 Supply</div>
  </section>
</body>
</html>
```